Real Estate Website

I am looking for a website design for a website that will be featuring real estate listings across Australia. It will be a website for a real estate agency that operates through all states in Australia.

We like the designs of https://www.brightnest.com.au/ and https://valtoria.example/

On the brightnest website, we like the sell, buy, sold tabs but would also like lease, and agents. We also need a button somewhere for 'Join Agent Pivola' and 'Login'

On the Valtoria site it has a concierge section and we want something like that on the home page.

The contact details to show in the footer are:

Shop 2217B
Level 1 Harbourgate Shopping Centre
87 Quillon Terrace
Merrowvale

Attached are various versions of the logo and some intro text to go on the home page.

```html
<!DOCTYPE html>
<html lang="en">
<head>
<meta charset="utf-8">
<title>Agent Pivola – Real Estate Across Australia</title>
<link rel="stylesheet" href="https://fonts.googleapis.com/css2?family=Poppins:wght@300;400;500;600;700&display=swap">
<style>
:root{
  --gold:#a98142;
  --gold-light:#c39a52;
  --brown:#74471c;
  --band:#ae8b47;
  --ink:#1b1b1b;
  --dark:#161616;
  --grey-bg:#efefef;
  --text:#333;
  --white:#fff;
}
*{box-sizing:border-box;margin:0;padding:0}
html,body{width:1200px;height:4193px;overflow:hidden}
body{font-family:"Poppins",sans-serif;color:var(--text);background:var(--white);position:relative}
.abs{position:absolute}
.btn{display:flex;align-items:center;justify-content:center;font-weight:600;text-transform:uppercase;letter-spacing:.3px;color:var(--white)}
.btn-gold{background:linear-gradient(90deg,var(--brown),var(--gold-light))}
.btn-brown{background:var(--brown)}

/* Wordmark: plain name in the text font with one circle beside it */
.wordmark{display:flex;align-items:center;gap:10px;color:var(--white);font-weight:600}
.wordmark .dot{display:block;border-radius:50%;background:var(--white)}

/* Hero */
.hero{left:0;top:0;width:1200px;height:652px;background:linear-gradient(180deg,#3d4a5c 0%,#5e6462 35%,#4a5238 60%,#3f6a24 80%,#2e4d1a 100%)}
.main-nav{left:75px;top:72px;display:flex;font-size:13px;font-weight:500;color:var(--white)}
.main-nav span{margin-right:50px}
.hero-brand{left:0;width:1200px;top:66px;justify-content:center;font-size:22px}
.hero-brand .dot{width:14px;height:14px}
.join{left:836px;top:62px;width:188px;height:42px;font-size:13px}
.login{left:1036px;top:62px;width:90px;height:42px;font-size:13px;border:2px solid var(--white)}
.welcome{left:0;width:1200px;top:240px;text-align:center;color:var(--white);font-weight:700;font-size:40px;line-height:1}
.welcome-name{left:0;width:1200px;top:284px;text-align:center;color:var(--white);font-weight:500;font-size:64px;letter-spacing:2px;line-height:1}
.tabs{left:164px;top:394px;display:flex;height:42px;font-size:13px;font-weight:600;color:var(--white)}
.tabs span{display:flex;align-items:center;justify-content:center;width:95px;background:#1c1c1c}
.tabs .active{background:var(--gold)}
.search{left:164px;top:438px;width:873px;height:46px;background:var(--white);display:flex;align-items:center}
.search .field{flex:1;display:flex;align-items:center;gap:8px;padding-left:14px;font-size:12px;color:#333}
.search .go{width:225px;height:46px;font-size:13px}

/* Category tiles */
.tile{top:716px;width:330px;height:336px;display:flex;align-items:center;justify-content:center}
.tile .frame{position:absolute;inset:12px;border:3px solid var(--white)}
.tile b{position:relative;color:var(--white);font-size:42px;font-weight:700;letter-spacing:1px}
.tile-sell{left:75px;background:linear-gradient(160deg,#9aa7a0,#3f6e72 60%,#1f4a50)}
.tile-buy{left:435px;background:linear-gradient(160deg,#b7aa98,#6f6254 60%,#4a3d30)}
.tile-buy .frame{border-color:var(--gold)}
.tile-sold{left:798px;background:linear-gradient(170deg,#6a4555,#8a8a88 45%,#3d5430)}

/* Featured */
.featured{left:0;top:1112px;width:1200px;height:724px;background:var(--grey-bg)}
.section-title{left:0;width:1200px;text-align:center;color:var(--ink);font-weight:600;font-size:40px}
.listing{top:1260px;width:330px;height:384px;background:var(--white);box-shadow:0 2px 8px rgba(0,0,0,.12)}
.listing .photo{height:234px}
.listing .body{padding:22px 14px}
.listing .tag{font-size:11px;font-weight:700;color:var(--ink)}
.listing .price{font-size:22px;font-weight:700;color:var(--brown);margin-top:2px}
.listing .addr{font-size:13px;color:var(--ink);margin-top:6px}
.listing .meta{display:flex;gap:18px;margin-top:12px;font-size:11px;font-weight:600;color:var(--ink)}
.listing .meta i{display:inline-block;width:13px;height:8px;background:var(--gold);margin-right:4px;border-radius:2px}
.arrow{width:26px;height:26px}
.view-all{left:493px;top:1711px;width:214px;height:52px;font-size:15px}

/* Concierge */
.concierge{left:75px;top:1893px;width:1052px;height:314px;border-radius:10px;background:linear-gradient(180deg,#3a3424,#8a6a34 55%,#6d4f22)}
.concierge h2{position:absolute;top:50px;width:100%;text-align:center;color:var(--white);font-size:40px;font-weight:600}
.concierge p{position:absolute;width:100%;text-align:center;color:var(--white);font-size:19px}
.concierge .btn{position:absolute;left:440px;top:210px;width:172px;height:49px;border:2px solid var(--white);background:rgba(0,0,0,.35);font-size:15px}

/* About */
.about{left:0;top:2269px;width:1200px;height:539px;background:linear-gradient(120deg,#8a9aa6 0%,#6b7a68 40%,#5d6c5a 70%,#9fb4b8 100%)}
.about-box{left:615px;top:2339px;width:512px;height:401px;background:rgba(22,22,22,.92);color:var(--white);text-align:center;padding:30px 26px}
.about-box h2{font-size:40px;font-weight:600;line-height:1.0}
.about-box p{font-size:14px;line-height:26px;margin-top:26px}
.about-box .btn{width:172px;height:52px;margin:22px auto 0;font-size:15px}

/* Reviews */
.review{top:2945px;width:328px;text-align:center}
.review .photo{height:192px}
.review .avatar{width:78px;height:78px;border-radius:50%;background:#8a7a6a;border:3px solid var(--white);margin:-39px auto 0;position:relative}
.review .name{color:var(--gold);font-weight:600;font-size:19px;margin-top:6px}
.review .stars{display:flex;justify-content:center;margin-top:2px}
.review h3{font-size:18px;font-weight:500;color:var(--ink);margin-top:6px}
.review p{font-size:13px;line-height:24px;color:var(--ink);margin-top:4px}
.reviews-btn{left:501px;top:3386px;width:198px;height:46px;font-size:15px}

/* Newsletter */
.newsletter{left:0;top:3502px;width:1200px;height:281px;background:var(--band)}
.news-brand{left:75px;top:3700px;font-size:32px}
.news-brand .dot{width:20px;height:20px}
.news-title{left:522px;top:3548px;color:var(--white);font-size:40px;font-weight:600}
.input{top:3621px;width:295px;height:47px;background:var(--white);font-size:13px;padding-left:14px;display:flex;align-items:center;color:#333}
.subscribe{left:524px;top:3678px;width:162px;height:49px;font-size:15px;background:#5e3510}

/* Footer */
.footer{left:0;top:3783px;width:1200px;height:410px;background:var(--dark)}
.f-col{top:3842px;color:var(--white)}
.f-col h4{color:var(--gold);font-size:21px;font-weight:600;margin-bottom:18px}
.f-col li{list-style:none;font-size:14px;margin-bottom:18px}
.f-contact li{margin-bottom:0;line-height:24px}
.f-contact .gold{color:var(--gold)}
.copyright{left:75px;top:4150px;font-size:12px;color:var(--white)}
.social{left:950px;top:4147px;display:flex;gap:18px}
.social span{width:22px;height:22px;border-radius:50%;background:var(--white);display:block}
</style>
</head>
<body>

<!-- HERO -->
<section class="abs hero" role="img" aria-label="Dusk photograph of a large two-storey family home with a green lawn"></section>
<nav class="abs main-nav"><span>SELL</span><span>BUY</span><span>SOLD</span><span>LEASE</span><span>AGENTS</span></nav>
<div class="abs wordmark hero-brand"><span class="dot"></span>Agent Pivola</div>
<div class="abs btn btn-gold join">Join Agent Pivola</div>
<div class="abs btn login">Login</div>
<div class="abs welcome">WELCOME TO</div>
<div class="abs welcome-name">AGENT PIVOLA</div>
<div class="abs tabs"><span class="active">SELL</span><span>BUY</span><span>SOLD</span></div>
<div class="abs search">
  <div class="field">
    <svg width="12" height="12" viewBox="0 0 12 12"><circle cx="5" cy="5" r="3.6" fill="none" stroke="#111" stroke-width="1.8"/><line x1="7.6" y1="7.6" x2="11" y2="11" stroke="#111" stroke-width="2"/></svg>
    Start typing to find your address...
  </div>
  <div class="btn btn-gold go">Get Property Estimate</div>
</div>

<!-- CATEGORY TILES -->
<div class="abs tile tile-sell" role="img" aria-label="Modern home with a swimming pool"><div class="frame"></div><b>SELL</b></div>
<div class="abs tile tile-buy" role="img" aria-label="Interior living room with chair and dining table"><div class="frame"></div><b>BUY</b></div>
<div class="abs tile tile-sold" role="img" aria-label="White house exterior at sunset"><div class="frame"></div><b>SOLD</b></div>

<!-- FEATURED LISTINGS -->
<section class="abs featured"></section>
<h2 class="abs section-title" style="top:1172px">Featured Listings</h2>

<article class="abs listing" style="left:75px">
  <div class="photo" role="img" aria-label="White two-storey home under a blue sky" style="background:linear-gradient(180deg,#5a7fb8,#b9c3cc 55%,#4c6a2e)"></div>
  <div class="body"><div class="tag">FOR SALE</div><div class="price">$525,000+</div><div class="addr">14 Wren Lane Apt. 896, Brisbane</div>
  <div class="meta"><span><i></i>3</span><span><i></i>1</span><span><i></i>8</span></div></div>
</article>
<article class="abs listing" style="left:435px">
  <div class="photo" role="img" aria-label="Blue modern home with double garage at dusk" style="background:linear-gradient(180deg,#8aa3b8,#3f4a66 55%,#7a7a72)"></div>
  <div class="body"><div class="tag">FOR SALE</div><div class="price">$525,000+</div><div class="addr">14 Wren Lane Apt. 896, Brisbane</div>
  <div class="meta"><span><i></i>3</span><span><i></i>1</span><span><i></i>8</span></div></div>
</article>
<article class="abs listing" style="left:798px">
  <div class="photo" role="img" aria-label="Dark grey modern home with garden" style="background:linear-gradient(180deg,#7aa7d8,#3a3f48 55%,#5d7a3a)"></div>
  <div class="body"><div class="tag">FOR SALE</div><div class="price">$525,000+</div><div class="addr">14 Wren Lane Apt. 896, Brisbane</div>
  <div class="meta"><span><i></i>3</span><span><i></i>1</span><span><i></i>8</span></div></div>
</article>

<svg class="abs arrow" style="left:34px;top:1437px" viewBox="0 0 26 26"><circle cx="13" cy="13" r="13" fill="#222"/><path d="M15 7l-6 6 6 6M9 13h10" stroke="#fff" stroke-width="2.4" fill="none"/></svg>
<svg class="abs arrow" style="left:1141px;top:1437px" viewBox="0 0 26 26"><circle cx="13" cy="13" r="13" fill="#a98142"/><path d="M11 7l6 6-6 6M17 13H7" stroke="#fff" stroke-width="2.4" fill="none"/></svg>
<div class="abs btn btn-brown view-all">View All Listing</div>

<!-- CONCIERGE -->
<section class="abs concierge" role="img" aria-label="Luxury villa with pool at golden hour">
  <h2>Agent Pivola Concierge</h2>
  <p style="top:118px">Looking buy, rent or sell something unique?</p>
  <p style="top:160px">Want competitive developer financing at great rates?</p>
  <div class="btn">Find Out More</div>
</section>

<!-- ABOUT -->
<section class="abs about" role="img" aria-label="Aerial view of a coastal city and harbour"></section>
<div class="abs about-box">
  <h2>About<br>Agent Pivola</h2>
  <p>Nemo enim ipsam voluptatem quia voluptas sit aspernatur aut odit aut fugit, sed quia consequuntur magni dolores eos qui ratione voluptatem sequi nesciunt. Neque porro quisquam est, qui dolorem ipsum quia dolor sit amet, consectetur, adipisci velit, sed quia non numquam eius modi tempora incidunt ut labore et dolore.</p>
  <div class="btn btn-gold">Find Out More</div>
</div>

<!-- REVIEWS -->
<h2 class="abs section-title" style="top:2855px">Customer Reviews</h2>

<article class="abs review" style="left:75px">
  <div class="photo" role="img" aria-label="Stone and brick family home" style="background:linear-gradient(180deg,#c9d3dc,#6a5a4e 55%,#4d6a34)"></div>
  <div class="avatar" role="img" aria-label="Reviewer portrait"></div>
  <div class="name">Liam Corbett</div>
  <div class="stars"><svg width="108" height="16" viewBox="0 0 108 16"><g fill="#a98142"><polygon points="8,0 10,6 16,6 11,9.5 13,15.5 8,12 3,15.5 5,9.5 0,6 6,6"/><polygon transform="translate(23 0)" points="8,0 10,6 16,6 11,9.5 13,15.5 8,12 3,15.5 5,9.5 0,6 6,6"/><polygon transform="translate(46 0)" points="8,0 10,6 16,6 11,9.5 13,15.5 8,12 3,15.5 5,9.5 0,6 6,6"/><polygon transform="translate(69 0)" points="8,0 10,6 16,6 11,9.5 13,15.5 8,12 3,15.5 5,9.5 0,6 6,6"/><polygon transform="translate(92 0)" points="8,0 10,6 16,6 11,9.5 13,15.5 8,12 3,15.5 5,9.5 0,6 6,6"/></g></svg></div>
  <h3>Nemo enim ipsam voluptatem</h3>
  <p>“ Neque porro quisquam est, qui dolorem ipsum quia dolor sit amet, consectetur, adipisci velit, sed quia non numquam eius modi..”</p>
</article>
<article class="abs review" style="left:435px">
  <div class="photo" role="img" aria-label="White home with lit porch at sunset" style="background:linear-gradient(180deg,#b86a6a,#d8d0c4 45%,#4a5a30)"></div>
  <div class="avatar" role="img" aria-label="Reviewer portrait"></div>
  <div class="name">Liam Corbett</div>
  <div class="stars"><svg width="108" height="16" viewBox="0 0 108 16"><g fill="#a98142"><polygon points="8,0 10,6 16,6 11,9.5 13,15.5 8,12 3,15.5 5,9.5 0,6 6,6"/><polygon transform="translate(23 0)" points="8,0 10,6 16,6 11,9.5 13,15.5 8,12 3,15.5 5,9.5 0,6 6,6"/><polygon transform="translate(46 0)" points="8,0 10,6 16,6 11,9.5 13,15.5 8,12 3,15.5 5,9.5 0,6 6,6"/><polygon transform="translate(69 0)" points="8,0 10,6 16,6 11,9.5 13,15.5 8,12 3,15.5 5,9.5 0,6 6,6"/><polygon transform="translate(92 0)" points="8,0 10,6 16,6 11,9.5 13,15.5 8,12 3,15.5 5,9.5 0,6 6,6"/></g></svg></div>
  <h3>Nemo enim ipsam voluptatem</h3>
  <p>“ Neque porro quisquam est, qui dolorem ipsum quia dolor sit amet, consectetur, adipisci velit, sed quia non numquam eius modi..”</p>
</article>
<article class="abs review" style="left:798px">
  <div class="photo" role="img" aria-label="Blue and white home glowing at dusk" style="background:linear-gradient(180deg,#d89a5a,#4a5a78 50%,#3a4a3a)"></div>
  <div class="avatar" role="img" aria-label="Reviewer portrait"></div>
  <div class="name">Liam Corbett</div>
  <div class="stars"><svg width="108" height="16" viewBox="0 0 108 16"><g fill="#a98142"><polygon points="8,0 10,6 16,6 11,9.5 13,15.5 8,12 3,15.5 5,9.5 0,6 6,6"/><polygon transform="translate(23 0)" points="8,0 10,6 16,6 11,9.5 13,15.5 8,12 3,15.5 5,9.5 0,6 6,6"/><polygon transform="translate(46 0)" points="8,0 10,6 16,6 11,9.5 13,15.5 8,12 3,15.5 5,9.5 0,6 6,6"/><polygon transform="translate(69 0)" points="8,0 10,6 16,6 11,9.5 13,15.5 8,12 3,15.5 5,9.5 0,6 6,6"/><polygon transform="translate(92 0)" points="8,0 10,6 16,6 11,9.5 13,15.5 8,12 3,15.5 5,9.5 0,6 6,6"/></g></svg></div>
  <h3>Nemo enim ipsam voluptatem</h3>
  <p>“ Neque porro quisquam est, qui dolorem ipsum quia dolor sit amet, consectetur, adipisci velit, sed quia non numquam eius modi..”</p>
</article>

<svg class="abs arrow" style="left:33px;top:3125px" viewBox="0 0 26 26"><circle cx="13" cy="13" r="13" fill="#222"/><path d="M15 7l-6 6 6 6M9 13h10" stroke="#fff" stroke-width="2.4" fill="none"/></svg>
<svg class="abs arrow" style="left:1141px;top:3125px" viewBox="0 0 26 26"><circle cx="13" cy="13" r="13" fill="#a98142"/><path d="M11 7l6 6-6 6M17 13H7" stroke="#fff" stroke-width="2.4" fill="none"/></svg>
<div class="abs btn btn-brown reviews-btn">View All Reviews</div>

<!-- NEWSLETTER -->
<section class="abs newsletter"></section>
<div class="abs wordmark news-brand"><span class="dot"></span>Agent Pivola</div>
<h2 class="abs news-title">Newsletter Subscribe</h2>
<div class="abs input" style="left:524px">Full Name</div>
<div class="abs input" style="left:832px">Enter Email Address</div>
<div class="abs btn subscribe">Subscribe</div>

<!-- FOOTER -->
<footer class="abs footer"></footer>
<div class="abs f-col" style="left:75px"><h4>Quick Links</h4><ul><li>Sell</li><li>Buy</li><li>Sold</li><li>Lease</li><li>Agents</li></ul></div>
<div class="abs f-col" style="left:342px"><h4>Sell</h4><ul><li>Duis aute irure</li><li>Dolor in reprehenderit</li><li>Voluptate</li></ul></div>
<div class="abs f-col" style="left:615px"><h4>Buy</h4><ul><li>Duis aute irure</li><li>Dolor in reprehenderit</li><li>Voluptate</li></ul></div>
<div class="abs f-col f-contact" style="left:882px;width:245px"><h4>Contact Us</h4><ul>
  <li>Shop 2217B</li>
  <li>Level 1 Harbourgate Shopping Centre</li>
  <li>87 Quillon Terrace</li>
  <li>Merrowvale</li>
  <li class="gold" style="margin-top:14px">+61 7 5550 1942</li>
  <li class="gold" style="margin-top:8px">hello@agentpivola.example</li>
</ul></div>
<div class="abs copyright">© 2025, CompanyName All Right Reserved &nbsp;|&nbsp;Privacy Policy</div>
<div class="abs social" aria-label="Social media links"><span></span><span></span><span></span><span></span><span></span></div>

</body>
</html>
```